Redesign This Psychology Website

We would like a slight redesign of this successful psychology (relationship counselling) website:

www.TheKelvaleClinic.com.au

We are updating the website, and we'd like a slight refresh of the design and style.

Please keep to very similar colours, and use the same logo. We're looking for around 10 page templates, however the main one is the home page.

Keep in mind, this website already converts quite well, so we want a new, fresh design in keeping with this one. Please don't bother designing something too extremely different.

thanks :)

Target Market(s)

couples who are looking for relationship counselling. Men and women, 25 - 70, across Australia

Industry/Entity Type

Psychology

Number of Pages Required

5+ page

Font styles to use
Sans Serif

Colors
87cfc6
b7a5cd
ec1f27
ffffff
cee9f5

Requirements
Must have
• a similar look to the current design, just looking for a slight refresh.
• Search bar
• Areas for lots of photos
• same logo
• lots of content areas
Nice to have
• great content areas, where we can display a lot of content and our areas.
Should not have
• no colors like orange, etc.
• should not have a totally different feel.

```html
<!DOCTYPE html>
<html lang="en">
<head>
<meta charset="utf-8">
<title>Kelvale Clinic – Relationship Counselling</title>
<link rel="stylesheet" href="https://fonts.googleapis.com/css2?family=Lato:wght@400;700;900&display=swap">
<style>
:root{
  --teal:#87cfc6;
  --teal-dark:#1d6c78;
  --purple:#b7a5cd;
  --purple-deep:#9c86bd;
  --red:#ec1f27;
  --sky:#cee9f5;
  --white:#ffffff;
  --ink:#333a3f;
  --muted:#6b7378;
  --line:#d9dde0;
  --foot:#eef0f1;
  --foot-bar:#e3e6e8;
}
*{box-sizing:border-box;margin:0;padding:0}
html,body{width:1200px;height:4045px;overflow:hidden}
body{font-family:'Lato',Arial,sans-serif;color:var(--ink);background:var(--white);position:relative}
a{color:inherit;text-decoration:none}

.topbar{height:38px;border-bottom:1px solid var(--line);display:flex;align-items:center;justify-content:space-between;padding:0 127px 0 148px;font-size:13px;color:var(--muted)}
.topbar-links{display:flex;height:100%}
.topbar-links a{display:flex;align-items:center;padding:0 12px;border-left:1px solid var(--line)}
.topbar-links a:last-child{border-right:1px solid var(--line)}

.header{height:118px;display:flex;align-items:center;padding:0 127px;position:relative}
.logo{display:flex;align-items:center;gap:12px;width:345px}
.logo-dot{width:46px;height:46px;border-radius:50%;background:var(--teal-dark)}
.logo-name{font-size:36px;font-weight:700;color:var(--teal-dark);letter-spacing:-.5px}
.search{width:351px;height:38px;border:1px solid var(--line);border-radius:3px;display:flex;align-items:center;gap:10px;padding:0 12px;font-size:14px;color:#9aa1a5}
.call{margin-left:auto;text-align:right}
.call-label{font-size:15px;color:var(--teal)}
.call-number{display:flex;align-items:center;gap:8px;font-size:27px;color:var(--teal-dark);font-weight:700}

.nav{height:74px;background:var(--teal);display:flex;padding:0 127px;justify-content:space-between}
.nav a{display:flex;align-items:center;text-align:center;color:var(--white);font-weight:700;font-size:16px;line-height:1.15;padding:0 10px;border-right:1px solid rgba(255,255,255,.45)}
.nav a:last-child{border-right:0}

.hero{height:323px;position:relative;overflow:hidden;background:linear-gradient(100deg,#8a9ba6 0%,#c9d3d8 35%,#e8eef1 60%,#b9c8d2 100%)}
.hero-title{position:absolute;left:127px;top:140px;color:var(--white);font-size:42px;font-weight:900;line-height:1.05;letter-spacing:.5px}
.hero-cost{position:absolute;left:660px;top:50px;width:460px;height:460px;border-radius:50%;background:var(--white);text-align:center;padding:70px 70px 0}
.hero-cost h2{font-size:31px;font-weight:400;color:var(--red);margin-bottom:10px}
.hero-cost .price{font-size:19px;line-height:1.35;margin-bottom:16px}
.hero-cost .note{font-size:14px;line-height:1.45}

.main{position:absolute;top:553px;left:127px;width:944px;display:flex;justify-content:space-between}
.listing{width:615px;padding-top:50px}
.listing h1{font-size:27px;font-weight:400;color:var(--ink)}
.listing .region{font-size:27px;color:var(--teal-dark);margin-bottom:22px}
.profile{height:288px;display:flex;gap:16px}
.profile-photo{flex:0 0 122px;height:122px;border-radius:50%;border:3px solid var(--teal);padding:5px;background:var(--white)}
.profile-photo span{display:block;width:100%;height:100%;border-radius:50%;background:linear-gradient(160deg,#d9b8a2,#8c6a58)}
.profile-body{flex:1;font-size:13px;line-height:1.45}
.profile-name{font-size:24px;color:var(--red);line-height:1.2;margin-bottom:4px}
.certified{color:var(--teal-dark);font-weight:700}
.bio{color:var(--muted);margin-top:2px}
.actions{display:flex;gap:10px;margin:14px 0 10px}
.btn{display:inline-flex;align-items:center;justify-content:center;height:38px;width:112px;font-size:13px;letter-spacing:.5px}
.btn-outline{border:1px solid var(--purple);color:var(--purple-deep)}
.btn-solid{background:var(--teal-dark);color:var(--white);font-weight:700}
.call-line{font-weight:700;font-size:12px}
.more{display:flex;justify-content:center;margin-top:6px}

.sidebar{width:305px;padding-top:46px}
.finder{background:var(--purple);height:364px;padding:22px 20px;color:var(--white)}
.finder h3{text-align:center;font-size:25px;line-height:1.2;margin-bottom:14px}
.finder label{display:block;font-size:13px;margin:8px 0 4px}
.finder .field{height:32px;background:var(--white);border-radius:2px;color:#8d9498;font-size:12px;display:flex;align-items:center;justify-content:space-between;padding:0 10px}
.finder .go{margin-top:16px;height:38px;background:var(--red);display:flex;align-items:center;justify-content:center;font-weight:700;font-size:17px}
.feature{height:238px;border:1px solid var(--line);margin-top:12px;display:flex;box-shadow:0 1px 3px rgba(0,0,0,.08)}
.feature+.feature{margin-top:24px}
.feature-text{width:50%;padding:24px 18px}
.feature-text h4{font-size:21px;line-height:1.2;margin-bottom:10px}
.feature-text p{font-size:11px;line-height:1.45;color:var(--muted);margin-bottom:12px}
.learn{display:inline-block;background:var(--purple-deep);color:var(--white);font-size:11px;padding:7px 12px}
.feature-img{width:50%}
.articles{margin-top:30px}
.article{height:116px;display:flex;gap:14px;margin-bottom:12px;border:1px solid var(--line)}
.article-img{width:150px}
.article-text{padding:14px 8px 0 0;font-size:14px;font-weight:700;line-height:1.3}
.article-text span{display:block;color:var(--teal-dark);font-weight:400;font-size:12px;margin-top:4px}
.categories{margin-top:12px;border:1px solid var(--line);height:884px}
.categories h3{background:var(--purple);color:var(--white);font-size:22px;text-align:center;height:66px;display:flex;align-items:center;justify-content:center}
.categories ul{list-style:none;padding:8px 18px}
.categories li{height:31px;border-bottom:1px solid #eceff0;display:flex;align-items:center;gap:10px;font-size:13px}
.categories li::before{content:"";border-left:6px solid var(--teal-dark);border-top:4px solid transparent;border-bottom:4px solid transparent}

.footer{position:absolute;top:3668px;left:0;width:1200px;height:297px;background:var(--foot);display:flex;padding:70px 127px 0 140px}
.footer .logo{width:320px;align-self:flex-start}
.footer-col{width:168px;font-size:14px;line-height:1.85}
.footer-col:nth-of-type(3){width:205px}
.footer-col h5{color:var(--teal-dark);font-size:17px;letter-spacing:.5px;margin-bottom:6px}
.social{display:flex;gap:8px;margin-top:10px}
.social span{width:30px;height:30px;border-radius:50%;background:var(--teal-dark)}
.social span:nth-child(2){background:#3a8fd1}
.social span:nth-child(4){background:var(--red)}
.copyright{position:absolute;top:3965px;left:0;width:1200px;height:80px;background:var(--foot-bar);display:flex;align-items:center;justify-content:center;font-size:13px;color:var(--muted)}
</style>
</head>
<body>

<div class="topbar">
  <a href="#">Join Our Associate Program →</a>
  <nav class="topbar-links"><a href="#">Home</a><a href="#">Cart</a><a href="#">Blog</a><a href="#">Resources</a><a href="#">Contact</a></nav>
</div>

<header class="header">
  <div class="logo"><span class="logo-dot"></span><span class="logo-name">Kelvale Clinic</span></div>
  <div class="search">
    <svg width="14" height="14" viewBox="0 0 14 14"><circle cx="6" cy="6" r="4.5" fill="none" stroke="#9aa1a5" stroke-width="1.6"/><line x1="9.3" y1="9.3" x2="13" y2="13" stroke="#9aa1a5" stroke-width="1.6"/></svg>
    Search here
  </div>
  <div class="call">
    <div class="call-label">Call Us Now</div>
    <div class="call-number">
      <svg width="22" height="22" viewBox="0 0 24 24"><path d="M6.6 10.8a15 15 0 0 0 6.6 6.6l2.2-2.2a1 1 0 0 1 1-.25 11.4 11.4 0 0 0 3.6.57 1 1 0 0 1 1 1V20a1 1 0 0 1-1 1A17 17 0 0 1 3 4a1 1 0 0 1 1-1h3.5a1 1 0 0 1 1 1c0 1.25.2 2.45.57 3.57a1 1 0 0 1-.25 1z" fill="#ec1f27"/></svg>
      1300 555 019
    </div>
  </div>
</header>

<nav class="nav">
  <a href="#">COUNSELLING<br>TYPES</a>
  <a href="#">RELATIONSHIP COUNSELLING<br>LOCATIONS</a>
  <a href="#">SEX THERAPY<br>LOCATIONS</a>
  <a href="#">ABOUT US</a>
  <a href="#">QUIZZES</a>
  <a href="#">FAQ'S</a>
  <a href="#">CONTACT</a>
</nav>

<section class="hero" role="img" aria-label="Photo of a couple in a counselling session">
  <div class="hero-title">RELATIONSHIP<br>COUNSELLING</div>
  <div class="hero-cost">
    <h2>Cost of Sessions</h2>
    <p class="price">$160 for 50 min session<br>($175 for after hours sessions or all sessions at CBD locations)</p>
    <p class="note">Please enquire for details on Private Health<br>Insurance rebates &amp; Medicare Rebates</p>
  </div>
</section>

<div class="main">
  <section class="listing">
    <h1>Relationship Counselling</h1>
    <div class="region">Near Sydney, New South Wales, Australia</div>

    <article class="profile">
      <div class="profile-photo" role="img" aria-label="Portrait of Tessa"><span></span></div>
      <div class="profile-body">
        <div class="profile-name">Tessa</div>
        <div>Registered Psychologist Sydney</div>
        <div>B.A. (Psych)(Hons), M. Comm, M.Psych, MAPS</div>
        <div class="certified">Kelvale Certified</div>
        <p class="bio">Tessa works in private practice, specialising in individual and relationship counselling. She has trained in couples counselling, mediation and psycho-dynamic therapy, and works with couples facing breakdowns, infidelity and separation.</p>
        <div class="actions"><a class="btn btn-outline" href="#">READ MORE</a><a class="btn btn-solid" href="#">BOOK NOW</a></div>
        <div class="call-line">Or to book an appointment, please call 1300 555 019</div>
      </div>
    </article>

    <article class="profile">
      <div class="profile-photo" role="img" aria-label="Portrait of Delia"><span></span></div>
      <div class="profile-body">
        <div class="profile-name">Delia</div>
        <div>Registered Psychologist Sydney</div>
        <div>B Arts (Psych), Grad Dip Rehab Couns</div>
        <div class="certified">Kelvale Certified</div>
        <p class="bio">Delia is a registered psychologist providing marriage counselling in Sydney. She has worked for over 15 years in the private and public sector, including education and private practice, with couples, adults and young people.</p>
        <div class="actions"><a class="btn btn-outline" href="#">READ MORE</a><a class="btn btn-solid" href="#">BOOK NOW</a></div>
        <div class="call-line">Or to book an appointment, please call 1300 555 019</div>
      </div>
    </article>

    <article class="profile">
      <div class="profile-photo" role="img" aria-label="Portrait of Paula"><span></span></div>
      <div class="profile-body">
        <div class="profile-name">Paula</div>
        <div>Registered Psychologist Sydney</div>
        <div>M Clin Psych, BSSc (Psych)(Hons), BSc Econ, MAPS</div>
        <div class="certified">Kelvale Certified</div>
        <p class="bio">Paula is a registered psychologist who works with individuals, couples and families. She has helped people with relationship difficulties for over twenty years in personal and workplace settings, and cares about people who are struggling.</p>
        <div class="actions"><a class="btn btn-outline" href="#">READ MORE</a><a class="btn btn-solid" href="#">BOOK NOW</a></div>
        <div class="call-line">Or to book an appointment, please call 1300 555 019</div>
      </div>
    </article>

    <article class="profile">
      <div class="profile-photo" role="img" aria-label="Portrait of Bronwyn"><span></span></div>
      <div class="profile-body">
        <div class="profile-name">Bronwyn</div>
        <div>Registered Psychologist Sydney</div>
        <div>B Soc Sci (Psych), B Soc Sci (Hons), Post Grad Dip Psych, Grad Dip Systemic Therapy, H Dip Ed.</div>
        <div class="certified">Infidelity Specialist</div>
        <p class="bio">Bronwyn specialises in relationship counselling in Sydney, with a special focus and interest in relationships. She has done extensive training in this area both locally and overseas.</p>
        <div class="actions"><a class="btn btn-outline" href="#">READ MORE</a><a class="btn btn-solid" href="#">BOOK NOW</a></div>
        <div class="call-line">Or to book an appointment, please call 1300 555 019</div>
      </div>
    </article>

    <article class="profile">
      <div class="profile-photo" role="img" aria-label="Portrait of Nadia"><span></span></div>
      <div class="profile-body">
        <div class="profile-name">Nadia</div>
        <div>Registered Psychologist Sydney</div>
        <div>BA, M Psych, MAPS</div>
        <div class="certified">Kelvale Certified</div>
        <p class="bio">Nadia is a psychologist with 25 years experience. She enjoys working with couples and families on relationship issues to improve skills in communication, problem solving and conflict resolution, helping people heal and grow.</p>
        <div class="actions"><a class="btn btn-outline" href="#">READ MORE</a><a class="btn btn-solid" href="#">BOOK NOW</a></div>
        <div class="call-line">Or to book an appointment, please call 1300 555 019</div>
      </div>
    </article>

    <article class="profile">
      <div class="profile-photo" role="img" aria-label="Portrait of Miranda"><span></span></div>
      <div class="profile-body">
        <div class="profile-name">Miranda</div>
        <div>Registered Psychologist Sydney</div>
        <div>BA (Psych), Grad Dip Sc (Psych), Grad Dip (App Psych), MA (Coaching Psychology)</div>
        <div class="certified">Kelvale Certified</div>
        <p class="bio">Miranda specialises in individual and relationship counselling in Sydney and has worked as a registered psychologist for 12 years in a variety of public and private settings, including as a college guidance counsellor.</p>
        <div class="actions"><a class="btn btn-outline" href="#">READ MORE</a><a class="btn btn-solid" href="#">BOOK NOW</a></div>
        <div class="call-line">Or to book an appointment, please call 1300 555 019</div>
      </div>
    </article>

    <article class="profile">
      <div class="profile-photo" role="img" aria-label="Portrait of Delia"><span></span></div>
      <div class="profile-body">
        <div class="profile-name">Delia</div>
        <div>Registered Psychologist Sydney</div>
        <div>B Arts (Psych), Grad Dip Rehab Couns</div>
        <div class="certified">Kelvale Certified</div>
        <p class="bio">Delia is a registered psychologist providing marriage counselling in Sydney. She has worked for over 15 years in the private and public sector, including education and private practice, with couples, adults and young people.</p>
        <div class="actions"><a class="btn btn-outline" href="#">READ MORE</a><a class="btn btn-solid" href="#">BOOK NOW</a></div>
        <div class="call-line">Or to book an appointment, please call 1300 555 019</div>
      </div>
    </article>

    <article class="profile">
      <div class="profile-photo" role="img" aria-label="Portrait of Celeste"><span></span></div>
      <div class="profile-body">
        <div class="profile-name">Celeste</div>
        <div>Registered Psychologist Sydney</div>
        <div>BA, M Sc, Grad Dip Psych, Post Grad Dip Psych, M Psych, MAPS</div>
        <div class="certified">Kelvale Certified</div>
        <p class="bio">Celeste specialises in relationship counselling in Sydney. She is a caring, empathic and intuitive person who provides a safe, peaceful and reflective space where people can deepen their understanding of themselves and their partner.</p>
        <div class="actions"><a class="btn btn-outline" href="#">READ MORE</a><a class="btn btn-solid" href="#">BOOK NOW</a></div>
        <div class="call-line">Or to book an appointment, please call 1300 555 019</div>
      </div>
    </article>

    <article class="profile">
      <div class="profile-photo" role="img" aria-label="Portrait of Joanne"><span></span></div>
      <div class="profile-body">
        <div class="profile-name">Joanne</div>
        <div>Clinical Psychologist Sydney</div>
        <div>B A Hons, M Psych Clin, PhD, MAPS, M College Clin Psych</div>
        <div class="certified">Kelvale Certified</div>
        <p class="bio">Joanne is a clinical psychologist with many years of experience in relationship counselling in Sydney, as both a counsellor and psychotherapist. She works with adults and young people from many cultural and social backgrounds.</p>
        <div class="actions"><a class="btn btn-outline" href="#">READ MORE</a><a class="btn btn-solid" href="#">BOOK NOW</a></div>
        <div class="call-line">Or to book an appointment, please call 1300 555 019</div>
      </div>
    </article>

    <article class="profile">
      <div class="profile-photo" role="img" aria-label="Portrait of Carmen"><span></span></div>
      <div class="profile-body">
        <div class="profile-name">Carmen</div>
        <div>Registered Psychologist Sydney</div>
        <div>B Psych (Hons), Grad Dip Int Comm, PhD, MAPS</div>
        <div class="certified">Kelvale Certified</div>
        <p class="bio">Dr Carmen is a registered psychologist in Sydney and a full member of her professional society. She specialises in couples counselling and marital preparation, and holds an honours degree and a PhD in psychology.</p>
        <div class="actions"><a class="btn btn-outline" href="#">READ MORE</a><a class="btn btn-solid" href="#">BOOK NOW</a></div>
        <div class="call-line">Or to book an appointment, please call 1300 555 019</div>
      </div>
    </article>

    <div class="more"><svg width="34" height="18" viewBox="0 0 34 18"><polyline points="2,2 17,15 32,2" fill="none" stroke="#b9bfc3" stroke-width="3"/></svg></div>
  </section>

  <aside class="sidebar">
    <div class="finder">
      <h3>Find Our Psychologist<br>Near You</h3>
      <label>Type of Counselling</label>
      <div class="field">Select <svg width="10" height="6" viewBox="0 0 10 6"><polyline points="1,1 5,5 9,1" fill="none" stroke="#8d9498" stroke-width="1.5"/></svg></div>
      <label>Location</label>
      <div class="field"></div>
      <label>Postcode</label>
      <div class="field"></div>
      <div class="go">SEARCH</div>
    </div>

    <div class="feature">
      <div class="feature-text"><h4>Rebates Available</h4><p>Find out which health fund and Medicare rebates may apply to your sessions.</p><a class="learn" href="#">Learn More</a></div>
      <div class="feature-img" role="img" aria-label="Warm sunset photo of a couple holding hands" style="background:linear-gradient(135deg,#f6e7c8,#e0a24a 60%,#7a3d1c)"></div>
    </div>
    <div class="feature">
      <div class="feature-text"><h4>GP Referral Info</h4><p>Learn how a referral from your GP can support your counselling plan.</p><a class="learn" href="#">Learn More</a></div>
      <div class="feature-img" role="img" aria-label="Photo of a smiling doctor" style="background:linear-gradient(135deg,#f2f5f7,#c9d7e0)"></div>
    </div>
    <div class="feature">
      <div class="feature-text"><h4>Anxiety and Depression</h4><p>Support for anxiety, low mood and stress within your relationships.</p><a class="learn" href="#">Learn More</a></div>
      <div class="feature-img" role="img" aria-label="Moody photo of a person holding their head" style="background:linear-gradient(135deg,#8a8f94,#3f4448)"></div>
    </div>

    <div class="articles">
      <div class="article"><div class="article-img" role="img" aria-label="Photo of two hands reaching" style="background:linear-gradient(135deg,#d8b99c,#8c6d55)"></div><div class="article-text">What can I do if I'm living with a Narcissist?<span>Read More</span></div></div>
      <div class="article"><div class="article-img" role="img" aria-label="Photo of a couple in conflict" style="background:linear-gradient(135deg,#a89b93,#4f4540)"></div><div class="article-text">Are You Living With a Steamroller?<span>Read More</span></div></div>
      <div class="article"><div class="article-img" role="img" aria-label="Photo of a couple sitting apart" style="background:linear-gradient(135deg,#c4c7c9,#6f7579)"></div><div class="article-text">Did Your Relationship Start on Rocky Ground?<span>Read More</span></div></div>
      <div class="article"><div class="article-img" role="img" aria-label="Photo of a couple talking" style="background:linear-gradient(135deg,#e0c3a8,#9b7455)"></div><div class="article-text">Why am I with a Narcissist?<span>Read More</span></div></div>
      <div class="article"><div class="article-img" role="img" aria-label="Photo of a person writing a letter" style="background:linear-gradient(135deg,#e7e2dc,#a89684)"></div><div class="article-text">Letter for a Partner Doubtful About Relationship Counselling<span>Read More</span></div></div>
      <div class="article"><div class="article-img" role="img" aria-label="Photo of a couple arm wrestling" style="background:linear-gradient(135deg,#e8d7c2,#b08a63)"></div><div class="article-text">What Are You Like in a Relationship?<span>Read More</span></div></div>
    </div>

    <div class="categories">
      <h3>Blogs Categories</h3>
      <ul>
        <li>Affairs</li><li>Assertiveness</li><li>Attachment</li><li>Break up</li><li>Communication</li><li>Compatibility</li><li>Controlling</li><li>Couples counselling</li><li>Empathy</li><li>Enneagram</li><li>Financial stress</li><li>Individual counselling for relationships</li><li>Infidelity</li><li>Intimacy</li><li>Marriage counselling</li><li>Narcissism</li><li>Personal growth</li><li>Personality</li><li>psychological wellbeing</li><li>Psychologist Interviews</li><li>Relationship counselling</li><li>Relationship happiness</li><li>Relationship problems</li><li>Singles</li><li>Uncategorized</li>
      </ul>
    </div>
  </aside>
</div>

<footer class="footer">
  <div class="logo"><span class="logo-dot"></span><span class="logo-name">Kelvale Clinic</span></div>
  <div class="footer-col"><h5>QUICK LINKS</h5>Home<br>About Us<br>Our Blogs<br>Shop Cart<br>Contact Us</div>
  <div class="footer-col"><h5>RESOURCES</h5>Counselling Type<br>Sex Therapy<br>Quizzes<br>FAQ<br>Relationship Counselling</div>
  <div class="footer-col"><h5>CONTACT US</h5>42 Harbour Lane Suite 5<br>1300 555 019<br>hello@kelvaleclinic.example
    <div class="social"><span></span><span></span><span></span><span></span></div>
  </div>
</footer>
<div class="copyright">© 2017 Company Name All right reserved</div>

</body>
</html>
```